Holiday Rental Company Flyer Design (DL not A5)

Note from Brandloom Administration: The category sizing selected is A5, however the project requires DL sized artwork. Please refer to the DL template link below while the 'Special Requirements' are updated accordingly.

Project Brief:
We need a double sided DL flyer designed for an up market Holiday Rental Company that portrays a personalised approach to property management. These are to be used for letter box drops to homes we're specifically targeting so the design should be modern, complimentary colour palette, uncluttered & visually appealing.

Please Download the DL Template from Quillora here: http://www.quillora.com.au/ql/ns/propath/UploadResources.aspx?selectedTab=0?pfid=KMT&pf_id=KMT&xnav=easypath-upload-image#Templates

Target Market(s)

Wealthy Home Owners

Industry/Entity Type

It Company

Other font styles liked:
• Avant Garde Extra Light & Demi

Colors
33b8a4

Requirements
Must have
• DL Flyer sizes (210mm width x 99mm width, plus 3mm bleed)
• Front: Logo, Main Image & Grab
• Back: Contact Details & Brief Description of our business
• Images: Ideally the main image should be the house with the pool but alternatively a lifestyle images could also be used.
Nice to have
• A creative designer!
Should not have
• Clutter & busy designs

```html
<!DOCTYPE html>
<html lang="en">
<head>
<meta charset="utf-8">
<title>Tidewater Stays – DL Flyer</title>
<link href="https://fonts.googleapis.com/css2?family=Raleway:wght@200&family=Lato:ital,wght@0,400;0,700;1,400&display=swap" rel="stylesheet">
<style>
  :root {
    --teal: #33b8a4;
    --teal-bright: #3cc9b4;
    --navy: #15123f;
    --navy-deep: #0f0d33;
    --white: #ffffff;
    --backdrop: #2a2a2a;
    --sea-light: #7fdde0;
    --sea-mid: #2fc4c9;
    --sea-deep: #19a9b4;
  }
  * { margin: 0; padding: 0; box-sizing: border-box; }
  html, body { width: 1200px; height: 1051px; overflow: hidden; }
  body { background: var(--backdrop); position: relative; font-family: "Lato", sans-serif; }

  .flyer { position: absolute; width: 554px; height: 781px; overflow: hidden; }

  /* Back side */
  .flyer--back { left: 44px; top: 48px; background: var(--navy); }
  .back__frame-line { position: absolute; background: var(--teal); }
  .back__frame-line--top-left { left: 14px; top: 63px; width: 93px; height: 1px; }
  .back__frame-line--top-right { left: 449px; top: 63px; width: 89px; height: 1px; }
  .back__frame-line--left { left: 14px; top: 63px; width: 1px; height: 577px; }
  .back__frame-line--right { left: 538px; top: 63px; width: 1px; height: 577px; }
  .back__node { position: absolute; top: 57px; width: 12px; height: 12px; border-radius: 50%; background: var(--white); }
  .back__node--left { left: 101px; }
  .back__node--right { left: 443px; }

  .brand { position: absolute; display: flex; align-items: center; gap: 18px; }
  .brand__dot { width: 50px; height: 50px; border: 1.5px solid var(--teal); border-radius: 50%; flex: none; }
  .brand__name { font-family: "Raleway", sans-serif; font-weight: 200; color: var(--teal); line-height: 1; }
  .back__brand { left: 145px; top: 36px; }
  .back__brand .brand__name { font-size: 34px; letter-spacing: 3px; }

  .back__photo { position: absolute; left: 0; top: 250px; width: 554px; height: 390px;
    background: linear-gradient(180deg, var(--navy) 0%, #2a2466 25%, #4a3f8a 50%, #3d63b5 78%, #2b74c9 100%); }

  .back__heading { position: absolute; left: 30px; top: 134px; font-size: 30px; font-weight: 400; color: var(--white); letter-spacing: -0.2px; }
  .back__col { position: absolute; font-size: 10.4px; line-height: 15px; color: var(--teal); }
  .back__col--1 { left: 27px; top: 173px; width: 170px; }
  .back__col--2 { left: 214px; top: 173px; width: 140px; }
  .back__col--3 { left: 368px; top: 143px; width: 180px; }
  .back__divider { position: absolute; top: 175px; width: 1px; height: 56px; background: var(--teal); }
  .back__divider--1 { left: 200px; }
  .back__divider--2 { left: 355px; }

  .contact { position: absolute; left: 268px; top: 262px; color: var(--white); }
  .contact__lead { font-style: italic; font-size: 12.4px; line-height: 17.5px; }
  .contact__phone { margin-top: 4px; font-size: 35px; font-weight: 700; color: var(--teal-bright); letter-spacing: -0.5px; }
  .contact__post { margin-top: 4px; font-size: 12.6px; font-weight: 700; }
  .contact__email { margin-top: 6px; font-size: 14px; }

  .back__strip { position: absolute; left: 0; top: 640px; width: 554px; height: 141px; background: var(--white); }
  .thumb { position: absolute; top: 14px; height: 116px; }
  .thumb--bath { left: 14px; width: 172px; background: linear-gradient(160deg, #c9cbc8, #9fa4a3); }
  .thumb--flowers { left: 188px; width: 175px; background: linear-gradient(90deg, #5b5f5a, #7a6e62 60%, #b84a2e 80%, #6b4a36); }
  .thumb--bedroom { left: 365px; width: 173px; background: linear-gradient(160deg, #e8d3ae, #d9b37a 50%, #c8cf3e 75%, #e3dccf); }

  /* Front side */
  .flyer--front { left: 613px; top: 214px;
    background: linear-gradient(180deg, var(--sea-light) 0%, #a8e2e6 22%, var(--sea-mid) 26%, var(--sea-deep) 50%, var(--sea-mid) 75%, #5fd3d8 100%); }
  .front__frame { position: absolute; left: 39px; top: 42px; width: 476px; height: 697px; border: 1px solid rgba(255,255,255,0.75); }
  .front__brand { position: absolute; left: 0; top: 100px; width: 554px; text-align: center; }
  .front__brand .brand__name { color: var(--white); font-size: 60px; letter-spacing: 9px; line-height: 62px; }
  .front__dot { position: absolute; left: 245px; top: 250px; width: 64px; height: 64px; border: 1.5px solid var(--white); border-radius: 50%; }
  .front__band { position: absolute; left: 39px; top: 371px; width: 476px; height: 92px; background: var(--white);
    display: flex; align-items: center; justify-content: center; text-align: center; }
  .front__tagline { color: var(--teal); font-size: 29px; line-height: 36px; font-weight: 400; }
  .front__url { position: absolute; left: 0; top: 708px; width: 554px; text-align: center; color: var(--white); font-size: 12px; font-weight: 700; letter-spacing: 3.4px; }
</style>
</head>
<body>

<section class="flyer flyer--back" aria-label="Flyer back side">
  <div class="back__photo" role="img" aria-label="Photo of a modern home at dusk with a lit swimming pool"></div>

  <div class="back__frame-line back__frame-line--top-left"></div>
  <div class="back__frame-line back__frame-line--top-right"></div>
  <div class="back__frame-line back__frame-line--left"></div>
  <div class="back__frame-line back__frame-line--right"></div>
  <div class="back__node back__node--left"></div>
  <div class="back__node back__node--right"></div>

  <div class="brand back__brand">
    <span class="brand__dot"></span>
    <span class="brand__name">TIDEWATER<br>STAYS</span>
  </div>

  <h2 class="back__heading">What we do differently!</h2>
  <p class="back__col back__col--1">Rather than relying upon a key safe or a central pick-up destination, a ‘Tidewater Stays’ staff member will greet guests upon arrival.</p>
  <span class="back__divider back__divider--1"></span>
  <p class="back__col back__col--2">Our ‘Meet &amp; Greet’ service provides home owners with an increased level of Security &amp; also allows us to:</p>
  <span class="back__divider back__divider--2"></span>
  <p class="back__col back__col--3">Prepare the home for their arrival (lights, heaters, music etc.) Establish a rapport &amp; help facilitate future bookings Reiterate their responsibilities to ensure the return of their bond</p>

  <div class="contact">
    <p class="contact__lead">If you’d like to know what your property<br>could achieve or require additional information,<br>please contact us on:</p>
    <p class="contact__phone">(03)5550 4172</p>
    <p class="contact__post">PO Box 48, Bayfield Victoria 3900</p>
    <p class="contact__email">email: stay@tidewaterstays.com.au</p>
  </div>

  <div class="back__strip">
    <div class="thumb thumb--bath" role="img" aria-label="Photo of a bathroom basin with white flowers"></div>
    <div class="thumb thumb--flowers" role="img" aria-label="Photo of a vase of orange flowers on a table"></div>
    <div class="thumb thumb--bedroom" role="img" aria-label="Photo of a bed with yellow cushions and a patterned throw"></div>
  </div>
</section>

<section class="flyer flyer--front" role="img" aria-label="Flyer front: photo of sea lions swimming in clear turquoise water">
  <div class="front__frame"></div>
  <div class="front__brand"><span class="brand__name">TIDEWATER<br>STAYS</span></div>
  <span class="front__dot"></span>
  <div class="front__band">
    <p class="front__tagline">Holiday Rental Management<br>With a Difference</p>
  </div>
  <p class="front__url">tidewaterstays.com.au</p>
</section>

</body>
</html>
```